Ridgeline Haul Carriers - Website

A clean, not cluttered informative website for our business. We specialize in the transportation of radioactive materials across North America. The site is mostly for information about our company and will not be used to attract business but will be used to attract employee's mainly drivers. Driver's are very hard to find in our area. One of the pages needs to be a job's posting page with an apply now button. Either an application can be filled out there or a resume can be uploaded which ever functionality works better. I would like a website that I can easily edit, ability to change text and photos.

Number of Pages Required

5+ page

Colors

Designer to choose colors to be used in the design.

Requirements
Must have
• Home - About - Services - Jobs - Contact pages
• A way prospective employee's can apply or upload their resume to be emailed to me
• Very clean apperance
Should not have
• I don't want it to be busy

```html
<!DOCTYPE html>
<html lang="en">
<head>
<meta charset="utf-8">
<title>Ridgeline Haul Carriers</title>
<link href="https://fonts.googleapis.com/css2?family=Montserrat:wght@500;600;700&family=Roboto:wght@400;500;700&display=swap" rel="stylesheet">
<style>
:root{
  --blue:#1767b7;
  --blue-dark:#0f5aa5;
  --ink:#1f2226;
  --grey:#6c7076;
  --light:#f3f4f6;
  --white:#ffffff;
  --line:#d6d9de;
}
*{box-sizing:border-box;margin:0;padding:0}
html,body{width:1200px;height:3422px;overflow:hidden}
body{position:relative;background:var(--white);font-family:'Roboto',sans-serif;color:var(--ink)}
.abs{position:absolute}

/* header */
.site-header{left:0;top:0;width:1200px;height:105px;background:var(--white)}
.brand{left:100px;top:34px;display:flex;align-items:center;gap:12px;font-family:'Montserrat',sans-serif;font-weight:700;font-size:22px;color:var(--blue);letter-spacing:.5px}
.brand-mark{width:26px;height:26px;background:var(--blue)}
.main-nav{left:486px;top:46px;display:flex;gap:36px;font-family:'Roboto',sans-serif;font-size:15px;font-weight:500;color:var(--ink)}
.main-nav .active{color:var(--blue)}
.quote-btn{left:974px;top:40px;width:134px;height:36px;background:var(--blue);color:var(--white);font-size:12px;font-weight:500;display:flex;align-items:center;justify-content:center;gap:8px}

/* hero */
.hero{left:0;top:105px;width:1200px;height:369px;background:linear-gradient(90deg,#fafafa,#e6e8eb)}
.hero-bg{left:0;top:0;width:640px;height:369px;background:linear-gradient(90deg,#f7f7f8 0%,#e9eaec 60%,#dfe1e4 100%);opacity:.9}
.hero-photo{left:560px;top:0;width:640px;height:369px;background:linear-gradient(160deg,#f0a24a 0%,#c9744a 30%,#7d6a6a 55%,#3f4450 100%);clip-path:polygon(67px 0,640px 0,640px 369px,0 369px)}
.hero-kicker{left:100px;top:112px;font-family:'Montserrat',sans-serif;font-weight:600;font-size:28px;color:#3b3e42}
.hero-title{left:100px;top:152px;font-family:'Montserrat',sans-serif;font-weight:700;font-size:31px;color:var(--blue)}
.hero-text{left:104px;top:212px;width:440px;font-size:14px;line-height:22px;color:var(--grey)}

/* hiring band */
.hire-band{left:0;top:474px;width:1200px;height:142px;background:var(--blue)}
.hire-text{left:96px;top:58px;font-family:'Montserrat',sans-serif;font-weight:700;font-size:19px;color:var(--white)}
.apply-btn{left:878px;top:53px;width:198px;height:46px;border:2px solid var(--white);color:var(--white);font-size:12px;font-weight:500;display:flex;align-items:center;justify-content:center;gap:10px}

/* audience cards */
.aud-frame{border:4px solid var(--blue)}
.aud-photo{overflow:hidden}
.aud-card-title{width:100%;text-align:center;font-family:'Montserrat',sans-serif;font-weight:600;font-size:29px;color:var(--white)}
.aud-card-text{width:100%;text-align:center;font-size:14.5px;line-height:22px;color:var(--white)}
.read-btn{width:134px;height:36px;background:var(--blue);color:var(--white);font-size:14px;display:flex;align-items:center;justify-content:center}

/* intro */
.section-title{width:1200px;left:0;text-align:center;font-family:'Montserrat',sans-serif;font-weight:600;font-size:44px;color:var(--ink)}
.title-rule{left:505px;width:190px;height:2px;background:var(--ink)}
.title-rule.blue{background:var(--blue)}
.intro-text{left:160px;top:1150px;width:880px;text-align:center;font-size:17px;line-height:39px;color:var(--grey)}

/* video */
.video-band{left:0;top:1323px;width:1200px;height:415px;background:linear-gradient(180deg,#2b3442 0%,#4a525c 45%,#6e5a3c 70%,#5a4a33 100%)}
.play{left:568px;top:1500px}

/* testimonials */
.testi-box{width:448px;height:212px;border:2px solid var(--blue);background:var(--white)}
.avatar{width:104px;height:104px;border-radius:50%;background:var(--blue);display:flex;align-items:center;justify-content:center}
.avatar span{display:block;width:86px;height:86px;border-radius:50%;background:linear-gradient(180deg,#c9a88c,#8c6e5a)}
.avatar.alt span{background:linear-gradient(180deg,#8e6b55,#4f3a2e)}
.quote-mark{font-family:'Montserrat',sans-serif;font-weight:700;font-size:48px;color:var(--blue);line-height:1}
.testi-text{width:300px;text-align:center;font-size:14px;line-height:19px;color:var(--grey)}
.testi-name{width:448px;text-align:center;font-size:17px;color:var(--ink);font-weight:500}
.dots{left:534px;top:2232px;display:flex;align-items:center;gap:0}
.dot{width:7px;height:7px;border-radius:50%;background:#c3c7cc}
.dot.on{background:var(--blue)}
.dot-gap{width:24px;height:1px;background:#c3c7cc}

/* blog */
.blog-band{left:0;top:2276px;width:1200px;height:616px;background:linear-gradient(180deg,#2a2e33 0%,#3a3f44 60%,#2f3236 100%)}
.blog-title{color:var(--white)}
.blog-card{width:313px;height:388px;background:var(--white)}
.blog-photo{left:0;top:0;width:313px;height:185px}
.blog-head{left:27px;top:212px;width:270px;font-family:'Montserrat',sans-serif;font-weight:600;font-size:16.5px;line-height:27px;color:var(--ink)}
.blog-text{left:27px;top:277px;width:270px;font-size:13.5px;line-height:19px;color:var(--grey)}
.blog-more{left:27px;top:348px;font-size:13px;font-weight:700;color:var(--blue)}

/* partners */
.partners{left:0;top:2892px;width:1200px;height:165px;background:var(--white)}
.partner{background:#cdd0d4}

/* footer */
.site-footer{left:0;top:3057px;width:1200px;height:365px;background:var(--blue);color:var(--white)}
.foot-brand{left:100px;top:112px;display:flex;align-items:center;gap:10px;font-family:'Montserrat',sans-serif;font-weight:700;font-size:19px;color:var(--white)}
.foot-brand .brand-mark{width:22px;height:22px;background:var(--white)}
.foot-head{font-family:'Montserrat',sans-serif;font-weight:700;font-size:14px;letter-spacing:1px}
.foot-list{list-style:none;font-size:12px;letter-spacing:.5px}
.foot-list li{display:flex;align-items:center;gap:10px}
.social-dot{width:22px;height:22px;border-radius:50%;background:rgba(255,255,255,.9)}
.foot-rule{left:80px;top:278px;width:1040px;height:1px;background:rgba(255,255,255,.45)}
.copyright{left:0;top:322px;width:1200px;text-align:center;font-size:12px;letter-spacing:.5px}
</style>
</head>
<body>

<header class="site-header abs">
  <div class="brand abs"><span class="brand-mark"></span>Ridgeline Haul Carriers</div>
  <nav class="main-nav abs">
    <span class="active">HOME</span><span>ABOUT US</span><span>SERVICES</span><span>JOB</span><span>CONTACT US</span>
  </nav>
  <div class="quote-btn abs">
    <svg width="13" height="13" viewBox="0 0 13 13"><rect x="1" y="2" width="11" height="10" fill="none" stroke="#fff" stroke-width="1.4"/><line x1="1" y1="5" x2="12" y2="5" stroke="#fff" stroke-width="1.4"/><line x1="4" y1="0" x2="4" y2="3" stroke="#fff" stroke-width="1.4"/><line x1="9" y1="0" x2="9" y2="3" stroke="#fff" stroke-width="1.4"/></svg>
    GET A QUOTE
  </div>
</header>

<section class="hero abs">
  <div class="hero-bg abs" role="img" aria-label="Faded row of parked trucks"></div>
  <div class="hero-photo abs" role="img" aria-label="Silver tanker truck on the road at sunset"></div>
  <p class="hero-kicker abs">WELCOME TO</p>
  <h1 class="hero-title abs">RIDGELINE HAUL CARRIERS</h1>
  <p class="hero-text abs">Sed ut perspiciatis unde omnis iste natus error sit voluptatem accusantium doloremque</p>
</section>

<section class="hire-band abs">
  <p class="hire-text abs">We're always looking to hire quality drivers to join the Ridgeline family</p>
  <div class="apply-btn abs">ONLINE APPLICATION
    <svg width="16" height="16" viewBox="0 0 13 13"><rect x="1" y="2" width="11" height="10" fill="none" stroke="#fff" stroke-width="1.3"/><line x1="1" y1="5" x2="12" y2="5" stroke="#fff" stroke-width="1.3"/><line x1="4" y1="0" x2="4" y2="3" stroke="#fff" stroke-width="1.3"/><line x1="9" y1="0" x2="9" y2="3" stroke="#fff" stroke-width="1.3"/></svg>
  </div>
</section>

<!-- Shippers card -->
<div class="aud-frame abs" style="left:96px;top:672px;width:440px;height:286px"></div>
<div class="aud-photo abs" role="img" aria-label="White trucks parked side by side under a cloudy sky" style="left:110px;top:662px;width:437px;height:284px;background:linear-gradient(180deg,#4a5260 0%,#6d747e 50%,#3d434b 100%)"></div>
<h2 class="aud-card-title abs" style="left:110px;top:710px;width:437px">SHIPPERS</h2>
<p class="aud-card-text abs" style="left:110px;top:768px;width:437px">Lorem Ipsum is simply dummy text of the<br>printing and typesetting industry.</p>
<div class="read-btn abs" style="left:261px;top:856px">Read more</div>

<!-- Drivers card -->
<div class="aud-frame abs" style="left:657px;top:672px;width:440px;height:286px"></div>
<div class="aud-photo abs" role="img" aria-label="Driver's hands on a truck steering wheel" style="left:671px;top:662px;width:437px;height:284px;background:linear-gradient(180deg,#3c4048 0%,#5a5e66 50%,#2e3136 100%)"></div>
<h2 class="aud-card-title abs" style="left:671px;top:710px;width:437px">DRIVERS</h2>
<p class="aud-card-text abs" style="left:671px;top:768px;width:437px">Lorem Ipsum is simply dummy text of the<br>printing and typesetting industry.</p>
<div class="read-btn abs" style="left:822px;top:856px">Read more</div>

<!-- intro -->
<h2 class="section-title abs" style="top:1044px">We Are Driven</h2>
<div class="title-rule blue abs" style="top:1113px"></div>
<p class="intro-text abs">Sed ut perspiciatis unde omnis iste natus error sit voluptatem accusantium doloremque laudantium, totam rem aperiam, eaque ipsa quae ab illo inventore veritatis et quasi architecto beatae vitae dicta sunt explicabo. Nemo enim ipsam voluptatem quia voluptas sit aspernatur aut odit aut fugit, sed quia</p>

<!-- video -->
<section class="video-band abs" role="img" aria-label="White box truck driving across open plains at dusk"></section>
<svg class="play abs" width="66" height="66" viewBox="0 0 66 66" aria-label="Play video"><circle cx="33" cy="33" r="29" fill="none" stroke="#fff" stroke-width="5"/><polygon points="26,19 26,47 48,33" fill="#fff"/></svg>

<!-- testimonials -->
<h2 class="section-title abs" style="top:1796px">Testimonials</h2>
<div class="title-rule abs" style="top:1864px"></div>

<div class="testi-box abs" style="left:146px;top:1985px"></div>
<div class="avatar abs" style="left:318px;top:1937px"><span role="img" aria-label="Portrait of customer"></span></div>
<div class="quote-mark abs" style="left:172px;top:2055px">&ldquo;</div>
<p class="testi-text abs" style="left:220px;top:2065px">Class aptent taciti sociosqu ad litora torquent per conubia nostra per inceptos hymenaeos Proin nulla arcu nonummy luctus</p>
<div class="quote-mark abs" style="left:505px;top:2095px">&rdquo;</div>
<p class="testi-name abs" style="left:146px;top:2135px">John Doe</p>

<div class="testi-box abs" style="left:633px;top:1985px"></div>
<div class="avatar alt abs" style="left:805px;top:1937px"><span role="img" aria-label="Portrait of customer"></span></div>
<div class="quote-mark abs" style="left:659px;top:2055px">&ldquo;</div>
<p class="testi-text abs" style="left:707px;top:2065px">Class aptent taciti sociosqu ad litora torquent per conubia nostra per inceptos hymenaeos Proin nulla arcu nonummy luctus</p>
<div class="quote-mark abs" style="left:992px;top:2095px">&rdquo;</div>
<p class="testi-name abs" style="left:633px;top:2135px">Marcus Hale</p>

<div class="dots abs"><span class="dot on"></span><span class="dot-gap"></span><span class="dot"></span><span class="dot-gap"></span><span class="dot"></span><span class="dot-gap"></span><span class="dot"></span><span class="dot-gap"></span><span class="dot"></span></div>

<!-- blog -->
<section class="blog-band abs" role="img" aria-label="Dim lineup of parked trucks"></section>
<h2 class="section-title blog-title abs" style="top:2316px">Our Blog</h2>
<div class="title-rule abs" style="top:2384px;background:#fff"></div>

<article class="blog-card abs" style="left:100px;top:2445px">
  <div class="blog-photo abs" role="img" aria-label="Driver in orange vest standing in front of a truck" style="background:linear-gradient(180deg,#d9dadc,#a9acb0)"></div>
  <h3 class="blog-head abs">Pellentesque faucibus Ut accumsan elit Maecenas</h3>
  <p class="blog-text abs">Class aptent taciti sociosqu ad litora torquent per conubia nostra per inceptos hymenaeos Proin nulla arcu</p>
  <span class="blog-more abs">READ MORE</span>
</article>
<article class="blog-card abs" style="left:440px;top:2445px">
  <div class="blog-photo abs" role="img" aria-label="Hands on a steering wheel inside a truck cab" style="background:linear-gradient(180deg,#8a8e94,#3f4247)"></div>
  <h3 class="blog-head abs">Duis non nunc Nulla rhoncus dictum metus Curabitur tristiq</h3>
  <p class="blog-text abs">Class aptent taciti sociosqu ad litora torquent per conubia nostra per inceptos hymenaeos Proin nulla arcu</p>
  <span class="blog-more abs">READ MORE</span>
</article>
<article class="blog-card abs" style="left:782px;top:2445px">
  <div class="blog-photo abs" role="img" aria-label="Row of blue trucks parked in a lot" style="background:linear-gradient(180deg,#cfe0ef 0%,#3f78b8 55%,#8c9096 100%)"></div>
  <h3 class="blog-head abs">Vivamus porttitor neque at volutpat rutrum purus nisi ele</h3>
  <p class="blog-text abs">Class aptent taciti sociosqu ad litora torquent per conubia nostra per inceptos hymenaeos Proin nulla arcu</p>
  <span class="blog-more abs">READ MORE</span>
</article>

<!-- partners -->
<section class="partners abs">
  <div class="partner abs" style="left:104px;top:56px;width:126px;height:56px;border-radius:6px"></div>
  <div class="partner abs" style="left:400px;top:70px;width:118px;height:28px;border-radius:4px"></div>
  <div class="partner abs" style="left:688px;top:66px;width:126px;height:30px;border-radius:4px;background:#e1e3e6"></div>
  <div class="partner abs" style="left:988px;top:54px;width:106px;height:56px;border-radius:4px"></div>
</section>

<!-- footer -->
<footer class="site-footer abs">
  <div class="foot-brand abs"><span class="brand-mark"></span>Ridgeline Haul Carriers</div>

  <h4 class="foot-head abs" style="left:354px;top:45px">CONTACT US</h4>
  <ul class="foot-list abs" style="left:358px;top:83px;line-height:30px">
    <li><svg width="10" height="10" viewBox="0 0 10 10"><polygon points="10,0 0,4 4,6 6,10" fill="#fff"/></svg>42 Harrow Lane, Unit 3</li>
    <li style="padding-left:20px">P.O. Box 318</li>
    <li style="padding-left:20px">Eastfield, Ontario, Canada</li>
    <li><svg width="10" height="11" viewBox="0 0 10 11"><path d="M2 0h2l1 3-1.5 1a6 6 0 0 0 3 3L7.5 5.5l2.5 1V9c0 1-1 2-2 2C3.5 11 0 7 0 2.5 0 1 1 0 2 0z" fill="#fff"/></svg>(555) 014-2276</li>
    <li><svg width="11" height="9" viewBox="0 0 11 9"><rect width="11" height="9" fill="#fff"/><polyline points="0,0 5.5,5 11,0" fill="none" stroke="#1767b7" stroke-width="1.2"/></svg>hiring@ridgelinehaul.example</li>
  </ul>

  <h4 class="foot-head abs" style="left:652px;top:45px">LINKS</h4>
  <ul class="foot-list abs" style="left:652px;top:83px;line-height:30px">
    <li>Terms of use</li><li>Privacy Policy</li><li>Cookie Policy</li><li>Disclaimer</li>
  </ul>

  <h4 class="foot-head abs" style="left:878px;top:45px">CONNECT WITH US</h4>
  <ul class="foot-list abs" style="left:878px;top:79px;line-height:44px">
    <li><span class="social-dot"></span>Community</li>
    <li><span class="social-dot"></span>Updates</li>
    <li><span class="social-dot"></span>Careers Network</li>
    <li><span class="social-dot"></span>Photo Feed</li>
  </ul>

  <div class="foot-rule abs"></div>
  <p class="copyright abs">Copyrights 2019. All rights reserved</p>
</footer>

</body>
</html>
```